Unique Business Card Design

Unique Business Card design for our orthotic and prosthetic company. Our logo is on our website, color is light blue. Unique shape (artificial leg shaped, vertical, etc..) preferred. Logo, business name, individual name and basic demographics needed.

Industry/Entity Type

Business

Contact Information for Business Card

Logo, Industry, Phone # Logo, "Prosthetic & Orthotic Services" Place to add individual name and contact info

Colors
cee9f5

Requirements
Must have
• The icon must be there, placement of "Prosthetic & Orthotic Services" can be moved
Nice to have
• Like the mix of light blue, and a little darker blue. One design included the icons from my website which was a nice touch

```html
<!DOCTYPE html>
<html lang="en">
<head>
<meta charset="utf-8">
<title>Stridewell Inc. – Business Card</title>
<link rel="stylesheet" href="https://fonts.googleapis.com/css2?family=Source+Sans+3:ital,wght@0,400;0,600;0,700;1,400&family=Crimson+Text:ital@1&display=swap">
<style>
  :root {
    --backdrop: #b4aea6;
    --card-light: #f7f7f6;
    --card-mid: #e6e5e3;
    --navy: #1b2d6b;
    --navy-deep: #0f1c4f;
    --navy-glow: #2c47a3;
    --ink: #3a3a3c;
    --rule: #1b2d6b;
  }
  html, body {
    margin: 0;
    padding: 0;
    width: 1200px;
    height: 834px;
    overflow: hidden;
    background: var(--backdrop);
  }
  .business-card {
    position: absolute;
    left: 235px;
    top: 210px;
    width: 730px;
    height: 413px;
    border-radius: 14px;
    overflow: hidden;
    background: linear-gradient(120deg, var(--card-light) 0%, #ffffff 45%, var(--card-mid) 100%);
    box-shadow: 0 6px 18px rgba(0,0,0,0.18);
    font-family: "Source Sans 3", "Helvetica Neue", Arial, sans-serif;
  }
  .brand-disc {
    position: absolute;
    left: 3px;
    top: -7px;
    width: 430px;
    height: 430px;
    border-radius: 50%;
    background: radial-gradient(circle at 62% 30%, var(--navy-glow) 0%, var(--navy) 45%, var(--navy-deep) 100%);
  }
  .edge-tab {
    position: absolute;
    right: -12px;
    top: 32px;
    width: 24px;
    height: 44px;
    border-radius: 50%;
    background: var(--navy);
  }
  .contact-block {
    position: absolute;
    right: 27px;
    top: 24px;
    text-align: right;
    color: var(--ink);
  }
  .person-name {
    margin: 0;
    font-size: 21px;
    font-weight: 700;
    color: var(--navy);
    line-height: 26px;
  }
  .person-name .credentials {
    font-size: 16px;
    font-weight: 600;
  }
  .person-email {
    margin: 3px 0 0;
    font-size: 16px;
    font-style: italic;
    line-height: 20px;
  }
  .address {
    margin: 38px 0 0;
    font-size: 17px;
    line-height: 26px;
    padding-right: 0;
  }
  .contact-list {
    list-style: none;
    margin: 3px 0 0;
    padding: 0;
    font-size: 17px;
  }
  .contact-list li {
    display: flex;
    justify-content: flex-end;
    align-items: center;
    gap: 8px;
    height: 30px;
  }
  .contact-list svg {
    width: 18px;
    height: 18px;
    fill: var(--navy);
  }
  .address span { display: block; padding-right: 26px; }
  .company {
    position: absolute;
    right: 34px;
    top: 304px;
    width: 282px;
    text-align: center;
  }
  .company-name {
    margin: 0;
    font-size: 31px;
    font-weight: 600;
    color: var(--navy);
    line-height: 34px;
    letter-spacing: 0.5px;
  }
  .company-rule {
    height: 2px;
    background: var(--rule);
    margin: 4px 0 6px;
  }
  .company-tagline {
    margin: 0;
    font-family: "Crimson Text", Georgia, serif;
    font-style: italic;
    font-size: 18px;
    color: var(--navy);
  }
</style>
</head>
<body>
  <article class="business-card">
    <div class="brand-disc"></div>
    <div class="edge-tab"></div>

    <section class="contact-block">
      <h1 class="person-name">Miriam Castellano<span class="credentials">, CO LPO</span></h1>
      <p class="person-email">Mcastellano@stridewellinc.com</p>
      <p class="address">
        <span>2280 W. 14th Ave.</span>
        <span>Hartford, CT 06103</span>
      </p>
      <ul class="contact-list">
        <li>555.014.2200
          <svg viewBox="0 0 24 24" aria-label="Phone"><path d="M6.6 10.8a15.1 15.1 0 0 0 6.6 6.6l2.2-2.2c.3-.3.7-.4 1-.2 1.1.4 2.3.6 3.6.6.6 0 1 .4 1 1V20c0 .6-.4 1-1 1A17 17 0 0 1 3 4c0-.6.4-1 1-1h3.5c.6 0 1 .4 1 1 0 1.3.2 2.5.6 3.6.1.3 0 .7-.2 1z"/></svg>
        </li>
        <li>555.014.2219
          <svg viewBox="0 0 24 24" aria-label="Fax"><path d="M7 3h10v5H7zM4 9h16a2 2 0 0 1 2 2v6h-4v4H6v-4H2v-6a2 2 0 0 1 2-2zm4 7v3h8v-3z"/></svg>
        </li>
        <li>555-016.4871
          <svg viewBox="0 0 24 24" aria-label="Mobile"><path d="M7 1h10a2 2 0 0 1 2 2v18a2 2 0 0 1-2 2H7a2 2 0 0 1-2-2V3a2 2 0 0 1 2-2zm0 3v15h10V4zm5 16.2a1 1 0 1 0 0 .1z"/></svg>
        </li>
        <li>www.stridewellinc.com
          <svg viewBox="0 0 24 24" aria-label="Website"><path d="M12 2a10 10 0 1 0 0 20 10 10 0 0 0 0-20zm-1 17.9A8 8 0 0 1 4.1 10L9 15v1a2 2 0 0 0 2 2zm6.9-2.5A2 2 0 0 0 16 16h-1v-3a1 1 0 0 0-1-1H8v-2h2a1 1 0 0 0 1-1V7h2a2 2 0 0 0 2-2v-.4a8 8 0 0 1 2.9 12.8z"/></svg>
        </li>
      </ul>
    </section>

    <section class="company">
      <h2 class="company-name">STRIDEWELL INC.</h2>
      <div class="company-rule"></div>
      <p class="company-tagline">Prosthetic &amp; Orthotic Services</p>
    </section>
  </article>
</body>
</html>
```